New Business Card Design Project

Use the flyer uploaded and website www.brightoakbuilders.com for inspiration.
List Our Services on Backside of business cards
Marcus Delling
Harborline Builders Inc.
Licensed General Contractors
858-471-6093

Contact Information for Business Card

Use the flyer uploaded and website www.brightoakbuilders.com for inspiration. List Our Services on Backside of business cards Marcus Delling Harborline Builders Inc. Licensed General Contractors 858-471-6093

```html
<!DOCTYPE html>
<html lang="en">
<head>
<meta charset="UTF-8">
<title>Harborline Builders — Business Card</title>
<link href="https://fonts.googleapis.com/css2?family=Cinzel:wght@400&family=Montserrat:wght@700&family=Lato:wght@400&family=Fjalla+One&display=swap" rel="stylesheet">
<style>
  :root {
    --stage: #2b2d31;
    --card: #141414;
    --card-edge: #1d1d1d;
    --ink: #ffffff;
    --ink-soft: #d9d9d9;
    --rule: #e6e6e6;
  }
  * { margin: 0; padding: 0; box-sizing: border-box; }
  html, body { width: 1200px; height: 900px; overflow: hidden; }
  body {
    background: var(--stage);
    display: flex;
    align-items: center;
    justify-content: center;
    gap: 50px;
  }
  .card {
    position: relative;
    width: 525px;
    height: 300px;
    background: var(--card);
    border: 1px solid var(--card-edge);
    border-radius: 16px;
    overflow: hidden;
    color: var(--ink);
  }
  .brand {
    position: absolute;
    display: flex;
    align-items: center;
    gap: 10px;
    font-family: "Cinzel", serif;
    font-weight: 400;
    color: var(--ink-soft);
    letter-spacing: 1px;
  }
  .brand-mark {
    width: 12px;
    height: 12px;
    border-radius: 50%;
    background: var(--ink-soft);
  }
  .card-front .brand { left: 34px; top: 42px; font-size: 24px; }
  .contact-block {
    position: absolute;
    left: 250px;
    top: 130px;
  }
  .person-name {
    font-family: "Montserrat", sans-serif;
    font-weight: 700;
    font-size: 27px;
    line-height: 1.1;
  }
  .person-title {
    font-family: "Montserrat", sans-serif;
    font-weight: 700;
    font-size: 15px;
    margin-top: 4px;
  }
  .divider {
    width: 130px;
    height: 1px;
    background: var(--rule);
    margin: 10px 0 12px;
  }
  .contact-line {
    display: flex;
    align-items: center;
    gap: 10px;
    font-family: "Lato", sans-serif;
    font-size: 15px;
    margin-bottom: 8px;
  }
  .contact-line svg { width: 14px; height: 14px; flex: none; }
  .card-back .brand { left: 120px; top: 28px; font-size: 20px; }
  .services {
    position: absolute;
    left: 34px;
    top: 78px;
    font-family: "Fjalla One", sans-serif;
  }
  .services-title { font-size: 17px; letter-spacing: 0.5px; margin-bottom: 6px; }
  .service-list { list-style: none; }
  .service-item {
    display: flex;
    align-items: center;
    gap: 7px;
    font-size: 13.5px;
    line-height: 20px;
  }
  .service-item svg { width: 11px; height: 11px; flex: none; }
</style>
</head>
<body>
  <section class="card card-front">
    <div class="brand"><span class="brand-mark"></span>Harborline Builders</div>
    <div class="contact-block">
      <div class="person-name">Marcus Delling</div>
      <div class="person-title">Licensed General Contractors</div>
      <div class="divider"></div>
      <div class="contact-line">
        <svg viewBox="0 0 16 16" aria-hidden="true"><path d="M4 1.5 6.5 4 5 6c.8 1.8 2.4 3.4 4.2 4.2l2-1.5 2.5 2.5-1.6 2.3C7 13.2 2.8 9 2 3.3Z" fill="none" stroke="#fff" stroke-width="1.5" stroke-linejoin="round"/></svg>
        <span>858-471-6093</span>
      </div>
      <div class="contact-line">
        <svg viewBox="0 0 16 16" aria-hidden="true"><circle cx="8" cy="8" r="6.5" fill="none" stroke="#fff" stroke-width="1.4"/><ellipse cx="8" cy="8" rx="2.8" ry="6.5" fill="none" stroke="#fff" stroke-width="1.2"/><path d="M1.5 8h13M2.5 5h11M2.5 11h11" stroke="#fff" stroke-width="1"/></svg>
        <span>www.brightoakbuilders.com</span>
      </div>
    </div>
  </section>

  <section class="card card-back">
    <div class="brand"><span class="brand-mark"></span>Harborline Builders</div>
    <div class="services">
      <div class="services-title">OUR SERVICES</div>
      <ul class="service-list">
        <li class="service-item"><svg viewBox="0 0 12 12" aria-hidden="true"><rect x="0.75" y="0.75" width="10.5" height="10.5" fill="none" stroke="#fff" stroke-width="1.3"/><path d="M3 6.2 5 8.2 9 3.8" fill="none" stroke="#fff" stroke-width="1.5"/></svg>Remodel: Kitchen &amp; Bath</li>
        <li class="service-item"><svg viewBox="0 0 12 12" aria-hidden="true"><rect x="0.75" y="0.75" width="10.5" height="10.5" fill="none" stroke="#fff" stroke-width="1.3"/><path d="M3 6.2 5 8.2 9 3.8" fill="none" stroke="#fff" stroke-width="1.5"/></svg>Painting: Interior &amp; Exterior</li>
        <li class="service-item"><svg viewBox="0 0 12 12" aria-hidden="true"><rect x="0.75" y="0.75" width="10.5" height="10.5" fill="none" stroke="#fff" stroke-width="1.3"/><path d="M3 6.2 5 8.2 9 3.8" fill="none" stroke="#fff" stroke-width="1.5"/></svg>Flooring: Carpet, Vinyl, Wood</li>
        <li class="service-item"><svg viewBox="0 0 12 12" aria-hidden="true"><rect x="0.75" y="0.75" width="10.5" height="10.5" fill="none" stroke="#fff" stroke-width="1.3"/><path d="M3 6.2 5 8.2 9 3.8" fill="none" stroke="#fff" stroke-width="1.5"/></svg>Window &amp; Door Replacement</li>
        <li class="service-item"><svg viewBox="0 0 12 12" aria-hidden="true"><rect x="0.75" y="0.75" width="10.5" height="10.5" fill="none" stroke="#fff" stroke-width="1.3"/><path d="M3 6.2 5 8.2 9 3.8" fill="none" stroke="#fff" stroke-width="1.5"/></svg>Plumbing: Repairs &amp; Upgrades</li>
        <li class="service-item"><svg viewBox="0 0 12 12" aria-hidden="true"><rect x="0.75" y="0.75" width="10.5" height="10.5" fill="none" stroke="#fff" stroke-width="1.3"/><path d="M3 6.2 5 8.2 9 3.8" fill="none" stroke="#fff" stroke-width="1.5"/></svg>Energy-Efficient Upgrades</li>
        <li class="service-item"><svg viewBox="0 0 12 12" aria-hidden="true"><rect x="0.75" y="0.75" width="10.5" height="10.5" fill="none" stroke="#fff" stroke-width="1.3"/><path d="M3 6.2 5 8.2 9 3.8" fill="none" stroke="#fff" stroke-width="1.5"/></svg>Deck &amp; Patio Construction</li>
      </ul>
    </div>
  </section>
</body>
</html>
```